Harborline Auto LLC

Car Dealer Customer Service
Address: 2874 Cresthaven Road, Shelbyville, TN 37162
web: www.harborlineautoxq.net
email: harborlineautoxq@mailnest.example
Phone: (931) 555-0148
Phone: (629) 555-0173

```html
<!DOCTYPE html>
<html lang="en">
<head>
<meta charset="utf-8">
<title>Harborline Auto – Business Card</title>
<link href="https://fonts.googleapis.com/css2?family=Archivo:wght@800&family=Arimo:wght@400;700&family=Oswald:wght@500&display=swap" rel="stylesheet">
<style>
  :root {
    --brand-blue: #1f7aa6;
    --brand-blue-deep: #1a6d95;
    --brand-yellow: #f0b23c;
    --ink: #222222;
    --paper: #f6f6f6;
    --backdrop: #dcdcdc;
    --rule: #bdbdbd;
  }
  * { box-sizing: border-box; margin: 0; padding: 0; }
  html, body { width: 1200px; height: 930px; overflow: hidden; }
  body {
    background: var(--backdrop);
    display: flex;
    flex-direction: column;
    align-items: center;
    justify-content: center;
    gap: 50px;
    font-family: "Arimo", Arial, sans-serif;
  }
  .card {
    width: 700px;
    height: 400px;
    position: relative;
    box-shadow: 0 6px 18px rgba(0,0,0,0.12);
  }
  .card--front { background: var(--paper); }
  .card--back {
    background: var(--brand-blue);
    display: flex;
    flex-direction: column;
    align-items: center;
    justify-content: center;
    gap: 22px;
  }
  .brand {
    display: flex;
    align-items: center;
    gap: 14px;
  }
  .brand__dot {
    width: 46px; height: 46px; border-radius: 50%;
    background: var(--brand-yellow);
    flex: none;
  }
  .brand__name {
    font-family: "Archivo", Arial, sans-serif;
    font-weight: 800;
    letter-spacing: 2px;
    text-transform: uppercase;
  }
  .card--back .brand__name { color: #ffffff; font-size: 40px; }
  .tagline {
    font-family: "Oswald", Arial, sans-serif;
    font-weight: 500;
    color: #ffffff;
    font-size: 22px;
    letter-spacing: 3px;
    text-transform: uppercase;
  }
  .front__brand {
    position: absolute;
    top: 62px; left: 0; right: 0;
    justify-content: center;
  }
  .card--front .brand__dot { background: var(--brand-blue); width: 40px; height: 40px; }
  .card--front .brand__name { color: var(--brand-blue); font-size: 32px; }
  .person {
    position: absolute;
    top: 150px; left: 0; right: 0;
    text-align: center;
  }
  .person__name {
    font-family: "Archivo", Arial, sans-serif;
    font-weight: 800;
    font-size: 24px;
    letter-spacing: 1.5px;
    color: var(--brand-blue);
    text-transform: uppercase;
  }
  .person__title {
    margin-top: 4px;
    font-size: 18px;
    color: var(--brand-yellow);
  }
  .contact {
    position: absolute;
    left: 50px; right: 40px; bottom: 50px;
    display: flex;
    align-items: stretch;
    gap: 20px;
    font-size: 15px;
    line-height: 1.55;
    color: var(--ink);
  }
  .contact__address { text-align: right; flex: 1; }
  .contact__web { color: var(--brand-blue-deep); }
  .contact__rule { width: 1px; background: var(--rule); }
  .contact__lines { flex: 1.25; list-style: none; }
  .contact__lines li { display: flex; align-items: center; gap: 8px; }
  .icon { width: 14px; height: 14px; flex: none; fill: var(--brand-blue); }
</style>
</head>
<body>

<section class="card card--front" aria-label="Business card front">
  <div class="brand front__brand">
    <span class="brand__dot"></span>
    <span class="brand__name">Harborline Auto</span>
  </div>

  <div class="person">
    <p class="person__name">Marcus Delaney</p>
    <p class="person__title">Managing Director</p>
  </div>

  <div class="contact">
    <div class="contact__address">
      <p>2874 Cresthaven Road</p>
      <p>Shelbyville, TN 37162</p>
      <p>www.<span class="contact__web">harborlineautoxq</span>.net</p>
    </div>
    <div class="contact__rule"></div>
    <ul class="contact__lines">
      <li>
        <svg class="icon" viewBox="0 0 24 24" aria-hidden="true"><path d="M6.6 10.8a15.1 15.1 0 0 0 6.6 6.6l2.2-2.2a1 1 0 0 1 1-.25 11.4 11.4 0 0 0 3.6.57 1 1 0 0 1 1 1V20a1 1 0 0 1-1 1A17 17 0 0 1 3 4a1 1 0 0 1 1-1h3.5a1 1 0 0 1 1 1c0 1.25.2 2.45.57 3.6a1 1 0 0 1-.25 1z"/></svg>
        (931) 555-0148
      </li>
      <li>
        <svg class="icon" viewBox="0 0 24 24" aria-hidden="true"><path d="M6.6 10.8a15.1 15.1 0 0 0 6.6 6.6l2.2-2.2a1 1 0 0 1 1-.25 11.4 11.4 0 0 0 3.6.57 1 1 0 0 1 1 1V20a1 1 0 0 1-1 1A17 17 0 0 1 3 4a1 1 0 0 1 1-1h3.5a1 1 0 0 1 1 1c0 1.25.2 2.45.57 3.6a1 1 0 0 1-.25 1z"/></svg>
        (629) 555-0173
      </li>
      <li>
        <svg class="icon" viewBox="0 0 24 24" aria-hidden="true"><path d="M2 5h20v14H2z M3.5 6.5 12 13l8.5-6.5" fill="var(--brand-blue)" stroke="#ffffff" stroke-width="1.4"/></svg>
        harborlineautoxq@mailnest.example
      </li>
    </ul>
  </div>
</section>

<section class="card card--back" aria-label="Business card back">
  <div class="brand">
    <span class="brand__dot"></span>
    <span class="brand__name">Harborline Auto</span>
  </div>
  <p class="tagline">Car Dealer Customer Service</p>
</section>

</body>
</html>
```